Fernhale Business Card Design

We are looking for a fresh business card design for our new logo. We would like a business card that is unique but friendly. We are in the window coverings business offering blinds, shutters and shades for homes.

Target Market(s)

Targeting the end-consumer

Industry/Entity Type

Business

Requirements
Must have
• Must have a dedicates space for a photo of our sales person. Must contain our new logo (attached).

```html
<!DOCTYPE html>
<html lang="en">
<head>
<meta charset="utf-8">
<title>Fernhale Business Card</title>
<link href="https://fonts.googleapis.com/css2?family=Work+Sans:wght@400;500;600&display=swap" rel="stylesheet">
<style>
  :root {
    --green: #7dc242;
    --ink: #5b5b5b;
    --ink-dark: #4a4a4a;
    --paper: #ffffff;
    --backdrop: #161616;
    --card-back-top: #1b1b1b;
    --card-back-bottom: #3a3a3a;
  }
  * { margin: 0; padding: 0; box-sizing: border-box; }
  html, body {
    width: 1200px; height: 897px; overflow: hidden;
    background: var(--backdrop);
    font-family: "Work Sans", Arial, sans-serif;
  }
  .stage { position: relative; width: 1200px; height: 897px; }
  .card {
    position: absolute; left: 303px; width: 594px; height: 338px; overflow: hidden;
  }
  .card-front { top: 92px; background: var(--paper); }
  .card-back {
    top: 469px;
    background: linear-gradient(160deg, var(--card-back-top) 0%, var(--card-back-top) 50%, var(--card-back-bottom) 100%);
  }

  .brand { position: absolute; display: flex; align-items: center; font-weight: 500; }
  .brand-square { display: block; background: var(--green); }
  .card-front .brand { left: 33px; top: 30px; height: 60px; color: var(--ink); font-size: 44px; letter-spacing: -0.5px; }
  .card-front .brand-square { width: 52px; height: 52px; margin-right: 20px; }
  .card-back .brand { left: 97px; top: 125px; height: 88px; color: #ffffff; font-size: 64px; letter-spacing: -0.5px; }
  .card-back .brand-square { width: 80px; height: 80px; margin-right: 26px; }

  .person { position: absolute; left: 34px; top: 138px; }
  .person-name { color: var(--green); font-size: 18px; font-weight: 600; letter-spacing: 0.8px; line-height: 22px; }
  .person-role { color: var(--ink); font-size: 13.5px; letter-spacing: 0.6px; line-height: 18px; }

  .contacts { position: absolute; left: 34px; top: 197px; list-style: none; }
  .contacts li { display: flex; align-items: center; height: 19.2px; color: var(--ink-dark); font-size: 13.5px; letter-spacing: 0.3px; }
  .contacts svg { width: 12px; height: 12px; margin-right: 16px; fill: var(--green); flex: none; }

  .address-band {
    position: absolute; left: 0; top: 306px; width: 318px; height: 32px;
    background: var(--green); color: #ffffff; font-size: 13.5px; letter-spacing: 0.3px;
    padding-left: 34px; line-height: 32px;
  }
  .portrait {
    position: absolute; left: 310px; top: 0; width: 284px; height: 338px;
    background: linear-gradient(180deg, #ffffff 0%, #f3f1ef 35%, #8a7a70 55%, #2e2e2e 75%, #262626 100%);
  }

  .back-web {
    position: absolute; left: 0; right: 0; top: 298px; text-align: center;
    color: #ffffff; font-size: 13.5px; letter-spacing: 1px;
  }
</style>
</head>
<body>
<main class="stage">
  <section class="card card-front">
    <div class="brand"><span class="brand-square"></span>Fernhale</div>

    <div class="person">
      <p class="person-name">DANA WHITLOW</p>
      <p class="person-role">REALTOR</p>
    </div>

    <ul class="contacts">
      <li><svg viewBox="0 0 12 12"><path d="M2.5 0.5 L4.5 3 L3.3 4.3 Q4.5 7 7.7 8.7 L9 7.5 L11.5 9.5 L10 11.5 Q4 11 0.5 2 Z"/></svg>(045) 218-7730</li>
      <li><svg viewBox="0 0 12 12"><path d="M3 0 H9 V12 H3 Z M4 1.5 V9.5 H8 V1.5 Z M5.5 10.3 H6.5 V11.2 H5.5 Z"/></svg>(045) 218-7731</li>
      <li><svg viewBox="0 0 12 12"><path d="M3 0 H9 V3 H3 Z M0.5 3.5 H11.5 V9 H9.5 V7 H2.5 V9 H0.5 Z M3 7.8 H9 V12 H3 Z"/></svg>(045) 218-7732</li>
      <li><svg viewBox="0 0 12 12"><path d="M0.5 2 H11.5 V3 L6 6.5 L0.5 3 Z M0.5 4.3 L6 7.8 L11.5 4.3 V10 H0.5 Z"/></svg>hello@fernhalehome.com</li>
      <li><svg viewBox="0 0 12 12"><path d="M6 0.5 A5.5 5.5 0 1 0 6.01 0.5 Z M6 1.5 A4.5 4.5 0 1 1 5.99 1.5 Z M5.5 1 H6.5 V11 H5.5 Z M1 5.5 H11 V6.5 H1 Z M3.5 2.5 H8.5 V3.3 H3.5 Z M3.5 8.7 H8.5 V9.5 H3.5 Z"/></svg>www.fernhalehome.com</li>
    </ul>

    <div class="portrait" role="img" aria-label="Photo of the sales person, smiling, in a dark blazer with arms crossed"></div>
    <div class="address-band">P.O.Box: 214, Lindmere, Westvale</div>
  </section>

  <section class="card card-back">
    <div class="brand"><span class="brand-square"></span>Fernhale</div>
    <p class="back-web">www.fernhaleliving.com</p>
  </section>
</main>
</body>
</html>
```